Web site for a company that sells Pinball machines

We need a website that is an online shopping experience for a Store that sells pinball machines and accessories. The name of the store is called "Gadget Arcade." The store it self has a showroom, but we would also like to have an Internet e-commerce presence. We pinball machines made by Vexler pinball. You can visit their website and see their current list of machines as well as their website for the machines that we are going to carry in our store. Their website is Vexlerpinball.com. I am able to use their machine photos as well as their machine brochure PDF files. I am also able to use their logo on my website two list it as a Vexler Authorized Dealer.
This website design needs to be funky, fun, very technologically oriented and modern. The people buying machines our spending anywhere between $5000 and $15,000 on one machine. These Are high-end buyers who are also usually fairly tech savvy or at least enjoy technology and graphics.
Attachments: I have attached photographs of some of my own machines which may be used in the website. I've also attached some downloaded files from Vexler pinball.com as well as some of their PDF files for brochures. I will carry all of their current models they have listed under games. Not the archived games. I have included one of their machines called Thunderwolf Limited edition in my photograph attachments. The rest of the photos are just random pictures that I have taken myself and maybe used to build the site. Lastly I have attached my logo which I am not super crazy about so I will also be posting a contest to redesign this logo. Tons more of my own pinball photos are available.
I would like for people to be able to purchase machines and accessories from the website, but also inform them to our actual showroom.
Updates
Project Deadline Extended Reason: Hello. We have extended five days due to some complications during the construction of our actual building. We were unable to participate in this web design during this time and so unfortunately were not able give feedback appropriately. We are back on track and will provide feedback to the designers who have designed up until this point. We will still be interested in seeing new submissions, however; this extension will give us a chance to provide feedback and coordinate the website appropriately. Thank you so much for your submissions and your patience!!!!Gadget Arcade Added Friday, April 21, 2017
Target Market(s)
Target market is 16 to 75. Techy individuals to enjoy gaming technology video animation and Vegas style twinkle
Industry/Entity Type
It Company
Coding
Coded - Design and coding required
Number of Pages Required
3 page
Font styles to use
Look and feel
Each slider illustrates characteristics of the customer's brand and the style your logo design should communicate.

```html
<!DOCTYPE html>
<html lang="en">
<head>
<meta charset="utf-8">
<title>Gadget Arcade – Pinball Machines and Accessories</title>
<link rel="stylesheet" href="https://fonts.googleapis.com/css2?family=Oswald:wght@300;400&display=swap">
<style>
  :root {
    --white: #ffffff;
    --ink: #333333;
    --accent: #d60a0a;
    --button: #e30613;
    --ring: #ffe600;
    --footer: #242424;
    --footer-text: #e6e6e6;
  }
  * { box-sizing: border-box; margin: 0; padding: 0; }
  a { text-decoration: none; color: inherit; }
  html, body { width: 1200px; height: 865px; overflow: hidden; }
  body { font-family: "Oswald", sans-serif; background: var(--white); position: relative; }

  .site-header {
    position: absolute; top: 0; left: 0; width: 1200px; height: 63px;
    background: var(--white); z-index: 3;
  }
  .nav-link {
    position: absolute; top: 22px; font-size: 16px; font-weight: 400;
    color: var(--ink); letter-spacing: 0.2px;
  }
  .nav-link.is-active { color: var(--accent); }
  .nav-search { position: absolute; left: 995px; top: 25px; }
  .nav-cart {
    position: absolute; left: 1036px; top: 17px; width: 32px; height: 32px;
    border-radius: 50%; background: var(--accent);
  }
  .nav-cart svg { position: absolute; left: 9px; top: 9px; }

  .brand-badge {
    position: absolute; left: 494px; top: -20px; width: 212px; height: 212px;
    border-radius: 50%; background: var(--white); z-index: 4;
    display: flex; align-items: center; justify-content: center; padding-top: 30px;
  }
  .brand-name {
    font-size: 26px; font-weight: 400; color: var(--ink);
    text-transform: uppercase; letter-spacing: 1px; text-align: center; line-height: 1.1;
  }

  .hero {
    position: absolute; top: 63px; left: 0; width: 1200px; height: 677px; overflow: hidden;
  }
  .hero-photo {
    position: absolute; inset: 0;
    background:
      radial-gradient(ellipse at 20% 40%, rgba(190,40,50,0.55), transparent 55%),
      radial-gradient(ellipse at 75% 25%, rgba(90,70,140,0.6), transparent 50%),
      radial-gradient(ellipse at 85% 70%, rgba(200,200,210,0.45), transparent 50%),
      radial-gradient(ellipse at 40% 80%, rgba(160,40,60,0.5), transparent 55%),
      linear-gradient(180deg, #3b2f46 0%, #5b3c4c 45%, #6d6470 100%);
  }
  .hero-shade { position: absolute; inset: 0; background: rgba(0,0,0,0.25); }

  .hero-title {
    position: absolute; top: 172px; left: 0; width: 1200px; text-align: center;
    font-size: 55px; font-weight: 400; color: var(--white); line-height: 1;
    letter-spacing: 0.3px;
  }
  .hero-tagline {
    position: absolute; top: 251px; left: 0; width: 1200px; text-align: center;
    font-size: 19.5px; font-weight: 300; color: var(--white);
  }
  .order-button {
    position: absolute; left: 518px; top: 303px; width: 164px; height: 49px;
    background: var(--button); color: var(--white); border-radius: 2px;
    font-size: 20px; font-weight: 300;
    display: flex; align-items: center; justify-content: center;
  }
  .slider-arrow { position: absolute; top: 345px; }
  .slider-arrow.prev { left: 132px; }
  .slider-arrow.next { left: 1044px; }

  .category {
    position: absolute; top: 391px; width: 190px; text-align: center;
    display: block; color: var(--white); text-decoration: none;
  }
  .category-image {
    width: 188px; height: 188px; border-radius: 50%; border: 4px solid var(--ring);
    margin: 0 auto;
  }
  .category-label {
    margin-top: 29px; font-size: 20px; font-weight: 300; color: var(--white);
    text-transform: uppercase; text-decoration: none;
  }
  .category.machines { left: 285px; }
  .category.accessories { left: 505px; }
  .category.featured { left: 729px; }
  .machines .category-image { background: radial-gradient(circle at 50% 40%, #c45a8a, #5a2a4a 60%, #2a1a2a); }
  .accessories .category-image { background: radial-gradient(circle at 50% 50%, #6a5aa0 0 18%, var(--white) 40%); }
  .featured .category-image { background: radial-gradient(circle at 45% 45%, #4a9ad0, #2a3a80 60%, #1a1a40); }

  .site-footer {
    position: absolute; top: 740px; left: 0; width: 1200px; height: 125px;
    background: var(--footer);
  }
  .social-links {
    position: absolute; top: 31px; left: 0; width: 1200px;
    display: flex; justify-content: center; gap: 18px;
  }
  .social-dot { width: 14px; height: 14px; border-radius: 50%; background: var(--footer-text); display: block; }
  .copyright {
    position: absolute; top: 75px; left: 0; width: 1200px; text-align: center;
    font-size: 12px; font-weight: 400; color: var(--footer-text); text-transform: uppercase;
  }
</style>
</head>
<body>
  <header class="site-header">
    <nav>
      <a class="nav-link is-active" href="#" style="left:210px">HOME</a>
      <a class="nav-link" href="#" style="left:294px">ABOUT US</a>
      <a class="nav-link" href="#" style="left:400px">PRODUCTS</a>
      <a class="nav-link" href="#" style="left:728px">NEWS</a>
      <a class="nav-link" href="#" style="left:808px">SUPPORT</a>
      <a class="nav-link" href="#" style="left:907px">CONTACT</a>
    </nav>
    <svg class="nav-search" width="16" height="16" viewBox="0 0 16 16" aria-label="Search">
      <circle cx="6.5" cy="6.5" r="4.8" fill="none" stroke="#333" stroke-width="2.2"/>
      <line x1="10" y1="10" x2="14" y2="14" stroke="#333" stroke-width="2.6" stroke-linecap="round"/>
    </svg>
    <a class="nav-cart" href="#" aria-label="Cart">
      <svg width="14" height="14" viewBox="0 0 14 14">
        <path d="M0 1.5h2.5l1.8 7h7.2l1.5-5H3.6" fill="none" stroke="#fff" stroke-width="1.8"/>
        <circle cx="5" cy="11.8" r="1.3" fill="#fff"/>
        <circle cx="10.5" cy="11.8" r="1.3" fill="#fff"/>
      </svg>
    </a>
  </header>

  <div class="brand-badge">
    <span class="brand-name">Gadget<br>Arcade</span>
  </div>

  <section class="hero">
    <div class="hero-photo" role="img" aria-label="Blurred close-up photo of a lit pinball playfield"></div>
    <div class="hero-shade"></div>
    <h1 class="hero-title">PINBALL MACHINES AND ACCESSORIES</h1>
    <p class="hero-tagline">OUR SPENDING ANYWHERE BETWEEN $5000 AND $15,000 ON ONE MACHINE.</p>
    <a class="order-button" href="#">ORDER NOW</a>

    <svg class="slider-arrow prev" width="26" height="48" viewBox="0 0 26 48" aria-label="Previous slide">
      <polyline points="24,1 2,24 24,47" fill="none" stroke="#fff" stroke-width="1.4"/>
    </svg>
    <svg class="slider-arrow next" width="26" height="48" viewBox="0 0 26 48" aria-label="Next slide">
      <polyline points="2,1 24,24 2,47" fill="none" stroke="#fff" stroke-width="1.4"/>
    </svg>

    <a class="category machines" href="#">
      <div class="category-image" role="img" aria-label="Photo of a colourful pinball playfield"></div>
      <div class="category-label">Pinball Machines</div>
    </a>
    <a class="category accessories" href="#">
      <div class="category-image" role="img" aria-label="Photo of a Thunderwolf Limited edition pinball cabinet"></div>
      <div class="category-label">Accessories</div>
    </a>
    <a class="category featured" href="#">
      <div class="category-image" role="img" aria-label="Photo of a blue pinball playfield with ramps"></div>
      <div class="category-label">Featured</div>
    </a>
  </section>

  <footer class="site-footer">
    <div class="social-links">
      <a class="social-dot" href="#" aria-label="Social link one"></a>
      <a class="social-dot" href="#" aria-label="Social link two"></a>
      <a class="social-dot" href="#" aria-label="Social link three"></a>
    </div>
    <p class="copyright">2017 © Gadget Arcade.all right reserved.</p>
  </footer>
</body>
</html>
```